Event flyer for Sunday night Youth Group

Need a 4 x 6 or 5 x 7 flyer for a new youth group starting on April 14. The youth group is for students in middle school and high school so it needs to look fun and cool, but not childish. I prefer it not to include pictures of people unless it's so obscure you can't really see their faces. I've uploaded some pictures of flyers I like. I've also attached a couple versions of our logo to use on the flyer.
Information the flyer needs to include:
Youth Group
Sundays, 6-8pm (beginning April 14)
Location: Marlowe's - 4219 Quarry Fern Ave N, Keizer, 97318
There will be dinner, games, friends, and a message.
Target Market(s)
Youth ages 13-18
Industry/Entity Type
Church
Font styles to use
Colors
Designer to choose colors to be used in the design.
Look and feel

```html
<!DOCTYPE html>
<html lang="en">
<head>
<meta charset="utf-8">
<title>Youth Group Flyer</title>
<link rel="stylesheet" href="https://fonts.googleapis.com/css2?family=Bebas+Neue&family=Poppins:wght@400;500;600;700&family=Allura&display=swap">
<style>
  :root{
    --teal-dark:#23444f;
    --teal-mid:#2f5865;
    --sage:#8a9a87;
    --orange:#f8935e;
    --orange-deep:#e07a3a;
    --gold:#f4b847;
    --paper:#f3f1ec;
    --stage:#e6e6e6;
    --label:#5d7a80;
    --white:#ffffff;
  }
  *{box-sizing:border-box;margin:0;padding:0}
  html,body{width:1200px;height:2400px;overflow:hidden}
  body{background:var(--stage);font-family:"Poppins",sans-serif;position:relative}
  .flyer{
    position:absolute;left:100px;top:500px;width:1000px;height:1400px;
    background:var(--paper);overflow:hidden;
    box-shadow:0 12px 30px rgba(0,0,0,.18);
  }
  .flyer-glow{
    position:absolute;inset:0;
    background:
      radial-gradient(ellipse 520px 420px at 72% 12%, rgba(255,236,170,.85), transparent 70%),
      radial-gradient(ellipse 420px 300px at 20% 60%, rgba(255,255,255,.8), transparent 70%),
      radial-gradient(ellipse 600px 500px at 50% 95%, rgba(225,225,225,.7), transparent 70%),
      linear-gradient(180deg,#f7f3e8 0%,#eeece8 55%,#e9e8e6 100%);
  }
  .brand{
    position:absolute;top:92px;left:0;width:100%;
    display:flex;justify-content:center;align-items:center;gap:22px;
  }
  .brand-mark{width:70px;height:70px;background:var(--teal-dark)}
  .brand-name{
    font-weight:600;font-size:40px;letter-spacing:2px;color:var(--teal-dark);
    text-transform:uppercase;
  }
  .headline{
    position:absolute;left:0;width:100%;
    font-family:"Bebas Neue",sans-serif;line-height:.78;
    -webkit-background-clip:text;background-clip:text;color:transparent;
    transform-origin:left top;white-space:nowrap;
  }
  .headline-youth{
    top:205px;left:118px;font-size:470px;width:auto;
    transform:rotate(-4deg) scaleX(.76);
    background-image:linear-gradient(100deg,var(--teal-mid) 0%,var(--orange-deep) 28%,#f6a24a 55%,var(--gold) 75%,#eb9a34 100%);
  }
  .headline-group{
    top:525px;left:150px;font-size:470px;width:auto;
    transform:rotate(-4deg) scaleX(.74);
    background-image:
      radial-gradient(ellipse 260px 380px at 48% 30%, rgba(246,160,70,.95), rgba(200,95,55,.6) 45%, transparent 75%),
      linear-gradient(180deg,#3a4e5c 0%,var(--teal-dark) 70%,#1f3d48 100%);
  }
  .intro{
    position:absolute;top:870px;left:52px;width:889px;height:80px;
    display:flex;align-items:center;gap:18px;
  }
  .intro-line{flex:1;height:3px;background:var(--orange)}
  .intro-word{font-family:"Allura",cursive;font-size:88px;color:#1d1d1d;line-height:1}
  .date-day{
    position:absolute;left:88px;top:960px;
    font-weight:700;font-size:142px;line-height:1;color:var(--teal-dark);letter-spacing:-4px;
  }
  .date-month{
    position:absolute;left:246px;top:988px;
    font-weight:700;font-size:64px;line-height:1;color:var(--teal-dark);
  }
  .date-year{
    position:absolute;left:246px;top:1053px;width:187px;height:46px;
    background:var(--sage);color:var(--white);
    font-weight:700;font-size:42px;line-height:46px;text-align:center;letter-spacing:3px;
  }
  .weekday{
    position:absolute;left:456px;top:966px;
    font-weight:500;font-size:42px;line-height:1;letter-spacing:12px;color:var(--teal-dark);
  }
  .time{
    position:absolute;left:456px;top:1010px;width:453px;height:72px;
    background:var(--orange);color:var(--white);
    font-weight:600;font-size:62px;line-height:74px;text-align:center;letter-spacing:5px;
  }
  .venue{
    position:absolute;left:81px;top:1103px;width:835px;height:52px;display:flex;
    font-weight:700;font-size:29px;line-height:52px;color:var(--white);
  }
  .venue-name{background:var(--sage);width:214px;text-align:center}
  .venue-address{background:var(--teal-dark);flex:1;text-align:center}
  .extras-title{
    position:absolute;left:104px;top:1186px;
    font-family:"Bebas Neue",sans-serif;font-size:78px;line-height:.84;
  }
  .extras-title .line-one{color:var(--teal-dark);display:block}
  .extras-title .line-two{color:var(--orange);display:block}
  .extras{position:absolute;top:1175px;left:0;width:100%;height:200px}
  .extra{position:absolute;width:140px;margin-left:-70px;text-align:center}
  .extra svg{width:106px;height:106px;display:block;margin:0 auto}
  .extra-label{font-size:22px;line-height:1;color:var(--label);margin-top:10px}
</style>
</head>
<body>
  <main class="flyer">
    <div class="flyer-glow" role="img" aria-label="Soft glowing bokeh light background in warm cream and white"></div>

    <header class="brand">
      <div class="brand-mark"></div>
      <div class="brand-name">Harborlight Fellowship</div>
    </header>

    <h1>
      <span class="headline headline-youth">YOUTH</span>
      <span class="headline headline-group">GROUP</span>
    </h1>

    <div class="intro">
      <span class="intro-line"></span>
      <span class="intro-word">Beginning</span>
      <span class="intro-line"></span>
    </div>

    <div class="date-day">14</div>
    <div class="date-month">APRIL</div>
    <div class="date-year">2024</div>
    <div class="weekday">SUNDAY</div>
    <div class="time">6PM - 8PM</div>

    <div class="venue">
      <span class="venue-name">MARLOWE'S</span>
      <span class="venue-address">4219 QUARRY FERN AVE N, KEIZER, 97318</span>
    </div>

    <div class="extras-title">
      <span class="line-one">THERE</span>
      <span class="line-two">WILL BE</span>
    </div>

    <section class="extras">
      <div class="extra" style="left:372px">
        <svg viewBox="0 0 106 106" fill="none" stroke="#2f5865" stroke-width="2.5" stroke-linecap="round">
          <circle cx="53" cy="53" r="50"/>
          <circle cx="53" cy="53" r="36" stroke-width="1.5"/>
          <path d="M42 33v14a5 5 0 0 0 10 0V33M47 33v40M62 33c-5 6-5 16 0 20v20"/>
        </svg>
        <div class="extra-label">Dinner</div>
      </div>
      <div class="extra" style="left:522px">
        <svg viewBox="0 0 106 106" fill="none" stroke="#2f5865" stroke-width="2.5" stroke-linecap="round" stroke-linejoin="round">
          <circle cx="53" cy="53" r="50"/>
          <path d="M34 42h38c6 0 9 5 10 12l2 10c1 6-6 9-10 4l-5-6H37l-5 6c-4 5-11 2-10-4l2-10c1-7 4-12 10-12z"/>
          <path d="M38 50v8M34 54h8"/>
          <circle cx="66" cy="51" r="1.8"/><circle cx="72" cy="56" r="1.8"/>
        </svg>
        <div class="extra-label">Games</div>
      </div>
      <div class="extra" style="left:672px">
        <svg viewBox="0 0 106 106" fill="none" stroke="#2f5865" stroke-width="2.5" stroke-linecap="round" stroke-linejoin="round">
          <circle cx="53" cy="53" r="50"/>
          <circle cx="40" cy="48" r="6"/><circle cx="66" cy="48" r="6"/>
          <path d="M28 74v-8c0-6 5-10 12-10s12 4 12 10v8M54 74v-8c0-6 5-10 12-10s12 4 12 10v8"/>
          <path d="M53 26v6M44 29l3 5M62 29l-3 5"/>
        </svg>
        <div class="extra-label">Friends</div>
      </div>
      <div class="extra" style="left:813px">
        <svg viewBox="0 0 106 106" fill="none" stroke="#2f5865" stroke-width="2.5" stroke-linecap="round" stroke-linejoin="round">
          <circle cx="53" cy="53" r="50"/>
          <path d="M53 54c-10-7-15-12-15-18a7 7 0 0 1 15-3 7 7 0 0 1 15 3c0 6-5 11-15 18z"/>
          <path d="M28 52l8 14h12v10M78 52l-8 14H58v10"/>
        </svg>
        <div class="extra-label">And a<br>Massage</div>
      </div>
    </section>
  </main>
</body>
</html>
```